Corporate Template

Looking for a set of corporate slides to be made which contain multiple different slides and orientations. Looking for at least 8 to 10 different master pages plus a Coversheet and closeout page. Incorporating a color palate similar to our logo coloring is preferred.
I have attached a logo.
I like the amber quill works designs best so far. They seem to fit what I'm looking for in terms of visual appearance.
Reason: I'm trying to allow time for a couple new designers to incorporate some changes I requested to their existing designs.

```html
<!DOCTYPE html>
<html lang="en">
<head>
<meta charset="utf-8">
<title>Closing Slide – Corvale Neurotech</title>
<link rel="stylesheet" href="https://fonts.googleapis.com/css2?family=Roboto:wght@400;500;700&display=swap">
<style>
  :root {
    --bg-center: #0aa0f5;
    --bg-mid: #1a73c7;
    --bg-edge: #0c3a70;
    --white: #ffffff;
    --accent: #5cc6f7;
    --divider: rgba(255, 255, 255, 0.22);
    --icon-text: #1579c9;
  }
  html, body {
    margin: 0;
    padding: 0;
    width: 1200px;
    height: 900px;
    overflow: hidden;
  }
  body {
    font-family: "Roboto", Arial, sans-serif;
  }
  .slide {
    position: relative;
    width: 1200px;
    height: 900px;
    overflow: hidden;
    background: radial-gradient(ellipse 62% 58% at 50% 52%, var(--bg-center) 0%, var(--bg-mid) 55%, var(--bg-edge) 100%);
    color: var(--white);
  }
  .brand-emblem {
    position: absolute;
    left: 413px;
    top: 121px;
    width: 374px;
    height: 374px;
  }
  .brand-emblem-name {
    position: absolute;
    left: 0;
    top: 0;
    width: 374px;
    height: 374px;
    display: flex;
    align-items: center;
    justify-content: center;
    text-align: center;
    font-weight: 700;
    font-size: 34px;
    line-height: 1.15;
    color: var(--white);
  }
  .social-list {
    position: absolute;
    top: 545px;
    left: 0;
    width: 1200px;
    display: flex;
    justify-content: center;
    gap: 14px;
    margin: 0;
    padding: 0;
    list-style: none;
  }
  .social-item {
    width: 66px;
    height: 66px;
    border-radius: 50%;
    background: var(--white);
    color: var(--icon-text);
    display: flex;
    align-items: center;
    justify-content: center;
    font-size: 11px;
    font-weight: 500;
  }
  .footer-divider {
    position: absolute;
    top: 730px;
    width: 1px;
    height: 132px;
    background: var(--divider);
  }
  .footer-divider.left { left: 305px; }
  .footer-divider.right { left: 895px; }
  .thanks {
    position: absolute;
    left: 78px;
    top: 772px;
    display: flex;
    align-items: center;
    gap: 6px;
  }
  .thanks-text {
    font-weight: 700;
    font-size: 22px;
    line-height: 0.95;
    color: var(--accent);
  }
  .thanks-text .big {
    display: block;
    font-size: 33px;
  }
  .thanks-icon {
    width: 60px;
    height: 60px;
    border-radius: 50%;
    background: var(--accent);
  }
  .contact {
    position: absolute;
    left: 305px;
    width: 590px;
    top: 742px;
    text-align: center;
  }
  .contact-web {
    font-weight: 700;
    font-size: 19px;
    margin: 0 0 22px;
  }
  .contact-address {
    font-size: 19px;
    margin: 0 0 14px;
    color: rgba(255, 255, 255, 0.92);
  }
  .contact-email {
    font-size: 19px;
    margin: 0;
    color: var(--accent);
  }
  .company-mark {
    position: absolute;
    left: 920px;
    top: 790px;
    width: 230px;
    text-align: center;
    font-weight: 700;
    font-size: 24px;
    color: var(--white);
  }
</style>
</head>
<body>
  <main class="slide">
    <div class="brand-emblem">
      <svg width="374" height="374" viewBox="0 0 374 374" aria-hidden="true">
        <circle cx="187" cy="187" r="169" fill="none" stroke="#ffffff" stroke-width="36"/>
      </svg>
      <div class="brand-emblem-name">Corvale<br>Neurotech</div>
    </div>

    <ul class="social-list" aria-label="Social channels">
      <li class="social-item">Folio</li>
      <li class="social-item">Chirpy</li>
      <li class="social-item">Plusline</li>
      <li class="social-item">Linkwork</li>
      <li class="social-item">Vidora</li>
    </ul>

    <div class="footer-divider left"></div>
    <div class="footer-divider right"></div>

    <div class="thanks">
      <div class="thanks-text">Thank<span class="big">you</span></div>
      <div class="thanks-icon" role="img" aria-label="Thumbs-up icon"></div>
    </div>

    <div class="contact">
      <p class="contact-web">http://corvaleneuro.net/</p>
      <p class="contact-address">1480 Larkspur Lane, Willow Bend, TX 75210</p>
      <p class="contact-email">hello@corvaleneuro.net</p>
    </div>

    <div class="company-mark">Corvale Neurotech</div>
  </main>
</body>
</html>
```